Gutschein-Design für Verkauf von Online-Schmuckstücken
Zielgruppe
Wir verkaufen Online Schmuckstücke!
www.silberfaden-shop.de
Aufgabenstellung
Wir haben eine schwarze Schachtel erstellt und da drinne wird eine Geschenkgutschein sein:
Es soll sehr schlicht sein und schwarzen Hintergrund haben.
Vorderseite nur unser LOGO.
Rückseite:
Betrag: _________
Gültig Bis: _________
Code: __________
Und unten klein gedruckt steht:
Diese Karte ist gültig nur auf der online shop seite www.silberfaden-shop.de und in unserer offizielen Stores. Dieses Karte ist nicht gültig bei rabatierte Produkten und man kann nicht mit dieser karte einen Gutscheinkarte kaufen.
Der Design soll sehr schlicht und dezenz sein.

```html
<!DOCTYPE html>
<html lang="de">
<head>
<meta charset="utf-8">
<title>Silberfaden – Geschenkgutschein</title>
<link rel="stylesheet" href="https://fonts.googleapis.com/css2?family=Open+Sans:wght@300;400&family=Yellowtail&family=Oswald:wght@400&display=swap">
<style>
  :root {
    --stage: #161515;
    --card-light: #2e2a2b;
    --card-dark: #151314;
    --card-edge: #f2f2f2;
    --ink: #f4f4f4;
    --accent: #f6ad3c;
  }
  * { box-sizing: border-box; margin: 0; padding: 0; }
  html, body { width: 1200px; height: 800px; overflow: hidden; }
  body {
    background: var(--stage);
    font-family: "Open Sans", Arial, sans-serif;
    color: var(--ink);
    position: relative;
  }
  .card {
    position: absolute;
    width: 640px;
    background: linear-gradient(135deg, var(--card-light), var(--card-dark) 70%);
    border: 1.5px solid var(--card-edge);
    box-shadow: 0 18px 40px rgba(0,0,0,0.6);
  }
  .card--back { left: 207px; top: 150px; height: 280px; }
  .card--front { left: 351px; top: 396px; height: 270px; }

  .voucher-frame {
    position: absolute;
    left: 108px; top: 52px;
    width: 423px; height: 143px;
    border: 1.5px solid var(--card-edge);
    border-top: none;
  }
  .voucher-frame::before,
  .voucher-frame::after {
    content: "";
    position: absolute;
    top: 0;
    height: 1.5px;
    background: var(--card-edge);
    width: 78px;
  }
  .voucher-frame::before { left: 0; }
  .voucher-frame::after { right: 0; }
  .voucher-title {
    position: absolute;
    left: 0; right: 0; top: 18px;
    text-align: center;
    font-family: "Yellowtail", "Brush Script MT", cursive;
    font-weight: 400;
    font-size: 56px;
    line-height: 1;
    color: var(--accent);
  }
  .voucher-fields {
    position: absolute;
    left: 0; right: 0; top: 96px;
    display: grid;
    grid-template-columns: 1fr 1fr;
    column-gap: 14px;
    row-gap: 1px;
    font-weight: 300;
    font-size: 16px;
    line-height: 22px;
    letter-spacing: 0.3px;
  }
  .voucher-fields dt { text-align: right; color: var(--ink); }
  .voucher-fields dd { text-align: left; color: var(--accent); }
  .voucher-terms {
    position: absolute;
    left: 140px; right: 140px; top: 206px;
    text-align: center;
    font-size: 7.5px;
    line-height: 10px;
    color: var(--ink);
  }
  .voucher-terms a { color: var(--accent); text-decoration: none; }

  .brand {
    position: absolute;
    left: 0; right: 0; top: 32px;
    display: flex;
    flex-direction: column;
    align-items: center;
  }
  .brand-mark {
    width: 100px; height: 100px;
    border-radius: 50%;
    background: var(--ink);
  }
  .brand-name {
    margin-top: 14px;
    font-weight: 300;
    font-size: 46px;
    letter-spacing: 2px;
    color: var(--ink);
    line-height: 1;
  }
  .brand-url {
    margin-top: 12px;
    font-family: "Oswald", "Arial Narrow", sans-serif;
    font-size: 15px;
    letter-spacing: 3px;
    color: var(--accent);
    line-height: 1;
  }
</style>
</head>
<body>
  <section class="card card--back" aria-label="Gutschein Rückseite">
    <div class="voucher-frame"></div>
    <h1 class="voucher-title">Gutschein</h1>
    <dl class="voucher-fields">
      <dt>BETRAG:</dt><dd>100 €</dd>
      <dt>GÜLTIG BIS:</dt><dd>01.03.2022</dd>
      <dt>CODE:</dt><dd>GSXXX22</dd>
    </dl>
    <p class="voucher-terms">Diese Karte ist gültig nur auf der Online Shop Seite <a>www.silberfaden-shop.de</a> und in unseren offiziellen Stores. Dieses Karte ist nicht gültig bei rabattierten Produkten und man kann nicht mit dieser Karte eine Gutscheinkarte kaufen.</p>
  </section>

  <section class="card card--front" aria-label="Gutschein Vorderseite">
    <div class="brand">
      <span class="brand-mark" aria-hidden="true"></span>
      <span class="brand-name">Silberfaden</span>
      <span class="brand-url">www.silberfaden-shop.de</span>
    </div>
  </section>
</body>
</html>
```